Business card design for Quorvane Engineering Tandem

We need a new business card design along with all the necessary to place an order. The company is Quorvane Engineering Tandem and we recently updated our logo.

```html
<!DOCTYPE html>
<html lang="en">
<head>
<meta charset="UTF-8">
<title>Quorvane Engineering Tandem – Business Card</title>
<link href="https://fonts.googleapis.com/css2?family=Montserrat:wght@400;500;700;800&display=swap" rel="stylesheet">
<style>
  :root {
    --stage: #2b2b2d;
    --card-front: #ffffff;
    --card-back: #8d8d8f;
    --brand-grey: #9b9b9b;
    --back-text: #c4c4c6;
    --gold: #e6b922;
    --ink: #1e1e1e;
  }
  * { margin: 0; padding: 0; box-sizing: border-box; }
  html, body {
    width: 1200px; height: 874px; overflow: hidden;
    background: var(--stage);
    font-family: "Montserrat", sans-serif;
  }
  .stage {
    width: 1200px; height: 874px;
    display: flex; flex-direction: column; align-items: center; justify-content: center;
    gap: 56px;
  }
  .card {
    width: 600px; height: 343px;
    border-radius: 26px;
    position: relative;
    overflow: hidden;
    box-shadow: 0 10px 24px rgba(0,0,0,.35);
  }
  .card--back { background: var(--card-back); }
  .card--front { background: var(--card-front); }

  .brand {
    position: absolute;
    display: flex; align-items: center; gap: 16px;
    font-weight: 800; text-transform: uppercase;
    letter-spacing: 1px; line-height: 1.1;
    white-space: nowrap;
  }
  .brand__mark { width: 26px; height: 26px; flex: none; }
  .card--back .brand { left: 82px; top: 128px; color: var(--back-text); font-size: 33px; }
  .card--back .brand__mark { background: var(--back-text); }
  .card--front .brand { left: 72px; top: 52px; color: var(--brand-grey); font-size: 33px; }
  .card--front .brand__mark { background: var(--gold); }

  .holder {
    position: absolute; left: 40px; top: 204px; width: 200px; text-align: right;
  }
  .holder__name { color: var(--gold); font-weight: 700; font-size: 21px; white-space: nowrap; }
  .holder__role { color: var(--ink); font-weight: 500; font-size: 14px; margin-top: 4px; }

  .divider {
    position: absolute; left: 258px; top: 196px; width: 1.5px; height: 76px;
    background: var(--gold);
  }
  .contacts {
    position: absolute; left: 276px; top: 200px;
    list-style: none; font-size: 15px; color: var(--ink); font-weight: 500;
  }
  .contacts li { display: flex; align-items: center; gap: 10px; height: 23px; white-space: nowrap; }
  .contacts svg { width: 13px; height: 13px; fill: var(--gold); flex: none; }
</style>
</head>
<body>
<main class="stage">
  <section class="card card--back" aria-label="Card back">
    <div class="brand"><span class="brand__mark"></span><span>Quorvane<br>Engineering Tandem</span></div>
  </section>

  <section class="card card--front" aria-label="Card front">
    <div class="brand"><span class="brand__mark"></span><span>Quorvane<br>Engineering Tandem</span></div>

    <div class="holder">
      <p class="holder__name">Marco Teixeira</p>
      <p class="holder__role">Managing Director</p>
    </div>
    <div class="divider"></div>
    <ul class="contacts">
      <li><svg viewBox="0 0 24 24"><path d="M6.6 10.8a15 15 0 0 0 6.6 6.6l2.2-2.2a1 1 0 0 1 1-.25 11.4 11.4 0 0 0 3.6.57 1 1 0 0 1 1 1V20a1 1 0 0 1-1 1A17 17 0 0 1 3 4a1 1 0 0 1 1-1h3.5a1 1 0 0 1 1 1c0 1.25.2 2.45.57 3.57a1 1 0 0 1-.25 1z"/></svg>(555)214-7780</li>
      <li><svg viewBox="0 0 24 24"><path d="M2 6h20v2.2l-10 6.3L2 8.2z M2 10.6l10 6.3 10-6.3V19H2z"/></svg>inffo@yourwebsitename.com</li>
      <li><svg viewBox="0 0 24 24"><circle cx="12" cy="12" r="10"/></svg>www.yourwebsitename.com</li>
    </ul>
  </section>
</main>
</body>
</html>
```